Recruitment of Trellan Staffing for the UK market

I want a website for the UK market to attract businesses and companies to come to us for Philipine labour. We want an information site that gives all information on what we do and how we can recruit Philippine labour.
This is a recruitment site for companies to contact us with their requirements for skilled workers coming from the Philipines over to the UK to work.

Target Market(s)

Uk Companies and businesses who want Philipine skilled workers

Industry/Entity Type

REcruitment

Coding

Number of Pages Required

5+ page

Font styles to use
Sans Serif

Colors
0054AA
0677BA
7BADD7
CADEEF
E8F1F8
0094D4
00A9DD
6FCCEA
C7EBF8
E9F6FB
EE7325
F08F49
F5BC92
FAE3D3
FDF4ED
EB3D1F
EC4F4E
F09395
F8D3D4
FCEDEE

Requirements
Must have
• Look professional and corperate with drop down menus for Home ,about, services,articles. training , contact us
Nice to have
• Look at Velmora recruitment- https://velmorarecruitment.example.co.uk/. This is my current site - https://www.trellanstaffing.example.com/
Should not have
• Cartoons or silly pictures , needs to be corperate looking

```html
<!DOCTYPE html>
<html lang="en">
<head>
<meta charset="utf-8">
<title>Trellan Staffing — Skilled Philippine Workers for UK Companies</title>
<link href="https://fonts.googleapis.com/css2?family=Poppins:wght@400;500;600&family=Anton&display=swap" rel="stylesheet">
<style>
:root{
  --blue:#0054AA;
  --blue-mid:#0677BA;
  --blue-pale:#E8F1F8;
  --blue-soft:#CADEEF;
  --orange:#EE7325;
  --orange-mid:#F08F49;
  --orange-soft:#F5BC92;
  --orange-pale:#FAE3D3;
  --orange-faint:#FDF4ED;
  --red:#EB3D1F;
  --navy:#0a1a3f;
  --ink:#111;
  --body:#333;
}
*{box-sizing:border-box;margin:0;padding:0}
html,body{width:1200px;height:4110px;overflow:hidden}
body{font-family:'Poppins',sans-serif;color:var(--body);background:#fff;position:relative}
section,header,footer{position:relative;width:1200px}
.abs{position:absolute}
.dots{display:flex;gap:4px}
.dots span{width:13px;height:13px;border-radius:50%}
.dots span:nth-child(1){background:var(--orange)}
.dots span:nth-child(2){background:var(--orange-soft)}
.dots span:nth-child(3){background:var(--orange-pale)}
h2.title{font-weight:500;font-size:34px;color:var(--ink);line-height:1.2}
p.copy{font-size:13.5px;line-height:30px;color:var(--body)}
.btn{display:inline-block;background:var(--blue);color:#fff;font-size:13.5px;padding:0 19px;line-height:36px}
.photo{border-radius:0}

/* header */
.site-header{height:77px;background:#fff}
.brand{left:166px;top:16px;display:flex;align-items:center;gap:8px;font-weight:600;font-size:22px;color:var(--blue)}
.brand i{width:14px;height:14px;background:var(--red);display:block}
.nav{right:160px;top:27px;display:flex;gap:34px;font-size:13.5px;color:#222}
.nav .active{color:var(--blue)}

/* hero */
.hero{height:451px;background:linear-gradient(90deg,#3a3026 0%,#4e4a45 40%,#2f3a44 100%)}
.hero-photo{inset:0;background:linear-gradient(100deg,#5a4a3c 0%,#3e5070 30%,#6b6a68 55%,#3a3a3a 100%);opacity:.9}
.hero h1{left:162px;top:200px;font-family:'Anton',sans-serif;font-weight:400;font-size:40px;line-height:48px;color:#fff;letter-spacing:.5px}
.hero h1 em{font-style:normal;color:var(--orange-soft);background:linear-gradient(transparent 78%,var(--red) 78%)}

/* quick contact form */
.quick-form{left:740px;top:153px;width:300px;height:410px;background:#fff;box-shadow:0 4px 14px rgba(0,0,0,.12);border:5px solid #888;border-bottom:none;border-right-color:#bbb;border-left-color:#888;z-index:5}
.quick-form .head{background:var(--blue);color:#fff;font-size:25px;font-weight:500;padding:10px 22px;height:58px}
.field{margin:10px 15px 0;background:var(--orange-faint);height:42px;font-size:12px;color:#222;padding:12px 18px}
.field.msg{height:92px}
.submit{margin:10px 15px 0;background:var(--orange);color:#fff;font-weight:600;font-size:16px;text-align:center;line-height:40px}

/* contact details & about */
.about{height:572px}
.details{left:161px;top:98px;width:337px;height:222px;background:var(--blue-pale)}
.details .head{background:var(--blue);color:#fff;font-size:25px;font-weight:500;padding:10px 21px;height:56px}
.details ul{list-style:none;padding:10px 22px 0 22px}
.details li{display:flex;gap:12px;font-size:12.5px;line-height:20px;color:#222;margin-bottom:10px;align-items:flex-start}
.details li svg{flex:none;margin-top:2px}
.details .rule{border-top:1px solid var(--blue-soft);margin:0 22px;padding-top:10px;display:flex;gap:8px}
.social{display:flex;gap:8px}
.social span{width:30px;height:30px;border-radius:50%;background:var(--blue);display:block;border:3px solid #fff;box-shadow:0 0 0 1px var(--blue)}
.about-text{left:584px;top:98px;width:460px}
.strip{left:161px;top:385px;width:879px;height:135px;display:flex}
.strip div{flex:1}

/* working together */
.working{height:500px}
.map{left:620px;top:40px;width:470px;height:400px;background:radial-gradient(ellipse at 55% 50%,#bcd7ee 0%,#e3eef8 45%,#fff 75%)}

/* what we do */
.whatwedo{height:490px}
.frame{left:146px;top:40px;width:413px;height:370px;background:var(--blue);clip-path:polygon(0 0,100% 0,95% 6%,4% 6%,4% 90%,0 100%)}
.office{left:161px;top:55px;width:413px;height:370px;background:linear-gradient(135deg,#d9dde2 0%,#b7bfc9 40%,#8895a6 70%,#e5e7ea 100%)}
.badge{left:486px;top:270px;width:135px;height:135px;border-radius:50%;background:#fff;border:10px solid var(--orange)}

/* how we help */
.help{height:613px}
.tile{top:48px;height:452px;width:322px}
.tile span{position:absolute;left:0;right:0;bottom:16px;text-align:center;color:#fff;font-size:16px}

/* split band */
.split{height:469px;display:flex}
.split .half{width:600px;height:469px;text-align:center;color:#fff;padding-top:120px}
.split .blue{background:linear-gradient(135deg,#0a63bd,var(--blue) 60%,#0b4d9a)}
.split .orange{background:linear-gradient(135deg,#f38037,var(--orange) 60%,#e06a1f)}
.split h2{font-size:34px;font-weight:600;margin:6px 0 14px}
.split p{font-size:13.5px;line-height:30px;width:520px;margin:0 auto}
.split .dots{justify-content:center}
.split .dots span{background:#fff}
.split .blue .dots span:nth-child(1),.split .blue .dots span:nth-child(2){background:var(--orange-soft)}
.split .orange .dots span:nth-child(1),.split .orange .dots span:nth-child(2){background:var(--orange-soft)}

/* service cards */
.cards{height:551px}
.card{top:113px;width:271px;height:326px;background:var(--blue-pale);text-align:center;padding-top:40px}
.card.featured{background:var(--blue);color:#fff}
.card h3{font-size:16px;font-weight:500;color:#111;margin:20px 0 10px}
.card.featured h3{color:#fff}
.card p{font-size:13px;line-height:22px;padding:0 22px;color:#222}
.card.featured p{color:#fff}
.card .btn{margin-top:22px;line-height:36px;font-size:13px;padding:0 20px}
.card.featured .btn{background:#fff;color:var(--blue)}

/* footer */
.site-footer{height:387px;background:var(--navy);color:#fff}
.site-footer .brand{left:162px;top:110px;color:#fff}
.site-footer .social{position:absolute;left:162px;top:172px}
.site-footer .social span{width:28px;height:28px}
.site-footer h4{font-size:16px;font-weight:500}
.links{left:440px;top:110px}
.links ul{list-style:none;display:grid;grid-template-columns:135px 100px;margin-top:8px}
.links li{font-size:13px;line-height:37px;border-bottom:1px solid #22325a}
.foot-contact{left:748px;top:110px;width:292px}
.foot-contact div{display:flex;gap:12px;font-size:12.5px;line-height:19px;padding:6px 0;border-bottom:1px solid #22325a}
.copyright{left:0;right:0;bottom:0;height:70px;border-top:1px solid #1d2c52;text-align:center;font-size:12.5px;line-height:70px}
</style>
</head>
<body>

<header class="site-header">
  <div class="abs brand"><i></i>Trellan Staffing</div>
  <nav class="abs nav">
    <span class="active">Home</span><span>About</span><span>Services</span><span>Articles</span><span>Training</span><span>Contact Us</span>
  </nav>
</header>

<section class="hero">
  <div class="abs hero-photo" role="img" aria-label="Smiling workers in hard hats in a factory"></div>
  <h1 class="abs">RECRUITING AND PLACING<br>SKILLED <em>PHILIPPINE WORKERS</em><br>INTO UK COMPANIES</h1>
</section>

<aside class="abs quick-form">
  <div class="head">Contact Us Today</div>
  <div class="field">Name*</div>
  <div class="field">Email*</div>
  <div class="field">Phone*</div>
  <div class="field msg">Message*</div>
  <div class="submit">SUBMIT NOW</div>
</aside>

<section class="about">
  <div class="abs details">
    <div class="head">Contact Details</div>
    <ul>
      <li><svg width="14" height="16" viewBox="0 0 14 16"><path d="M7 0a5.5 5.5 0 0 0-5.5 5.5C1.5 10 7 16 7 16s5.5-6 5.5-10.5A5.5 5.5 0 0 0 7 0z" fill="#0054AA"/><circle cx="7" cy="5.5" r="2" fill="#E8F1F8"/></svg>Larkspur Court, Eastmere Eastmere<br>EM4 2 United Kingdom</li>
      <li><svg width="16" height="16" viewBox="0 0 16 16"><path d="M3 1l3 3-2 2c1 2 3 4 5 5l2-2 3 3-2 3C6 14 2 10 1 4z" fill="none" stroke="#0054AA" stroke-width="1.5"/></svg>07700900418</li>
      <li><svg width="16" height="12" viewBox="0 0 16 12"><rect x=".75" y=".75" width="14.5" height="10.5" fill="none" stroke="#0054AA" stroke-width="1.5"/><path d="M1 1l7 6 7-6" fill="none" stroke="#0054AA" stroke-width="1.5"/></svg>sales@trellanstaffing.example.com</li>
    </ul>
    <div class="rule"><div class="social"><span></span><span></span><span></span><span></span></div></div>
  </div>
  <div class="abs about-text">
    <div class="dots"><span></span><span></span><span></span></div>
    <h2 class="title" style="margin:8px 0 20px">What The Business is About</h2>
    <p class="copy">We source skilled workers directly from the Philippines to work in the UK. With offices , training locations and specialist recruiters we can find the highest quality individuals to add value and resources to any UK buisness. We delivery quality based on vast experience over a number of years.</p>
  </div>
  <div class="abs strip">
    <div role="img" aria-label="Medical staff in a hospital" style="background:linear-gradient(135deg,#dfe8ef,#9db8d4)"></div>
    <div role="img" aria-label="Team of workers in blue uniforms" style="background:linear-gradient(135deg,#6fa0cf,#3c6fa6)"></div>
    <div role="img" aria-label="Workers in hard hats" style="background:linear-gradient(135deg,#c9b08a,#6d7c8f)"></div>
    <div role="img" aria-label="Engineers inspecting equipment" style="background:linear-gradient(135deg,#7c8790,#c8cdd2)"></div>
  </div>
</section>

<section class="working">
  <div class="abs" style="left:162px;top:114px;width:360px">
    <div class="dots"><span></span><span></span><span></span></div>
    <h2 class="title" style="margin:8px 0 16px">Working Together</h2>
    <p style="font-size:16px;line-height:30px;color:#222">We recruit the finest talent available with our dedicated 200 strong team.<br>Our centres are highlighted in <b style="color:var(--red);text-decoration:underline">Red Dots</b> on the map.</p>
    <span class="btn" style="margin-top:20px">Contact Us Today</span>
  </div>
  <div class="abs map" role="img" aria-label="Map of the Philippines marking centres in Baguio, Manila, Batangas, Bacolod and Davao"></div>
</section>

<section class="whatwedo">
  <div class="abs frame"></div>
  <div class="abs office" role="img" aria-label="Two businessmen reviewing work at an office computer"></div>
  <div class="abs badge" role="img" aria-label="20 years badge"></div>
  <div class="abs" style="left:651px;top:100px;width:390px">
    <div class="dots"><span></span><span></span><span></span></div>
    <h2 class="title" style="margin:8px 0 16px">What We Do</h2>
    <p class="copy">Our company has been estabilished in the Philippines for over 20 years. We have mainly been recruiting philippine workers for the off shore industry in asia but since brexit and the new rules on skilled workers entering the UK we have been working with UK companies who now have chance to recruit some of the finest hard working talent from the Philippines for their companies..</p>
  </div>
</section>

<section class="help">
  <div class="abs" style="left:162px;top:72px;width:300px">
    <div class="dots"><span></span><span></span><span></span></div>
    <h2 class="title" style="margin:8px 0 16px">How We Help</h2>
    <p class="copy">We work with companies to find skilled workers that meet the UK requirements for Visas and work permits. We guide you through the whole process and deliver highly trained people that add value to your business. We are here to help both the companies and the Philippino people to gain a better standard of living for their families.</p>
    <span class="btn" style="margin-top:16px">Contact Us Today</span>
  </div>
  <div class="abs tile" style="left:527px;background:linear-gradient(160deg,#9aa3a8,#4a5560 60%,#2c3540)" role="img" aria-label="Engineer in a hard hat operating machinery"><span>Equipment Engineer</span></div>
  <div class="abs tile" style="left:878px;background:linear-gradient(160deg,#6f8a70,#8c7a55 55%,#4a4a40)" role="img" aria-label="Two construction managers on a building site"><span>Building and Construction</span></div>
</section>

<section class="split">
  <div class="half blue">
    <div class="dots"><span></span><span></span><span></span></div>
    <h2>Where To Start</h2>
    <p>We need to know what your issues are and how we can understand the personnal you require, over what time frame and the number of employees you need. Once this is estabilished we start sourcing workers in the Philippines that meet your criteria while starting the process in the UK to be able to have all the documents in place to deliver your company hard working skilled individuals.</p>
  </div>
  <div class="half orange">
    <div class="dots"><span></span><span></span><span></span></div>
    <h2>Contact Us Today</h2>
    <p>Please contact us today with your requirements, this can be care workers, chef, welders, pipe fitters, caravan cabinet makers, medical workers. The UK list of required skills is extensive and the Philippines offersenglish speaking highly qualified hard working employees. Contact us today and make that first step to a highly motivated , quality skilled workforce.</p>
  </div>
</section>

<section class="cards">
  <div class="abs card" style="left:161px">
    <svg width="54" height="54" viewBox="0 0 54 54" fill="none" stroke="#0054AA" stroke-width="2"><rect x="10" y="8" width="30" height="40"/><rect x="18" y="4" width="14" height="8" fill="#E8F1F8"/><path d="M15 20h4M15 28h4M15 36h4M23 20h12M23 28h12M23 36h8"/><circle cx="42" cy="38" r="5"/><path d="M34 52c0-5 4-8 8-8s8 3 8 8"/></svg>
    <h3>UK Skilled Workers List</h3>
    <p>The UK government since brexit have developed a new system based on points...</p>
    <span class="btn">Read More</span>
  </div>
  <div class="abs card featured" style="left:465px">
    <svg width="54" height="54" viewBox="0 0 54 54" fill="none" stroke="#fff" stroke-width="2"><rect x="14" y="6" width="28" height="40"/><path d="M24 14h12M24 20h12M24 28h12M24 36h8"/><circle cx="14" cy="36" r="6"/><path d="M12 36l2 2 3-4"/></svg>
    <h3>Sponsor Licence</h3>
    <p>If you have areas of your business that meet the entry requirements of skilled labour...</p>
    <span class="btn">Read More</span>
  </div>
  <div class="abs card" style="left:768px">
    <svg width="54" height="54" viewBox="0 0 54 54" fill="none" stroke="#0054AA" stroke-width="2"><circle cx="24" cy="10" r="5"/><path d="M16 34V22c0-3 3-5 8-5s8 2 8 5v4"/><circle cx="36" cy="38" r="10"/><path d="M36 32v6l4 3"/><path d="M8 48h38"/></svg>
    <h3>Recruitment Timeline</h3>
    <p>Brief us on the job profiles-this is passed on to our teams in the Philippines.</p>
    <span class="btn">Read More</span>
  </div>
</section>

<footer class="site-footer">
  <div class="abs brand"><i></i>Trellan Staffing</div>
  <div class="social"><span></span><span></span><span></span><span></span></div>
  <div class="abs links">
    <h4>Quick Links</h4>
    <ul>
      <li>› Home</li><li>› Articles</li>
      <li>› About</li><li>› Training</li>
      <li>› Services</li><li>› Contact Us</li>
    </ul>
  </div>
  <div class="abs foot-contact">
    <h4 style="margin-bottom:8px">Contact Details</h4>
    <div><svg width="14" height="16" viewBox="0 0 14 16"><path d="M7 0a5.5 5.5 0 0 0-5.5 5.5C1.5 10 7 16 7 16s5.5-6 5.5-10.5A5.5 5.5 0 0 0 7 0z" fill="#fff"/><circle cx="7" cy="5.5" r="2" fill="#0a1a3f"/></svg><span>Larkspur Court, Eastmere Eastmere<br>EM4 2 United Kingdom</span></div>
    <div><svg width="16" height="16" viewBox="0 0 16 16"><path d="M3 1l3 3-2 2c1 2 3 4 5 5l2-2 3 3-2 3C6 14 2 10 1 4z" fill="none" stroke="#fff" stroke-width="1.5"/></svg>07700900418</div>
    <div style="border:none"><svg width="16" height="12" viewBox="0 0 16 12"><rect x=".75" y=".75" width="14.5" height="10.5" fill="none" stroke="#fff" stroke-width="1.5"/><path d="M1 1l7 6 7-6" fill="none" stroke="#fff" stroke-width="1.5"/></svg>sales@trellanstaffing.example.com</div>
  </div>
  <div class="abs copyright">© 2023 Trellan Staffing Ltd. All Rights Reserved</div>
</footer>

</body>
</html>
```